Design WordPress Website for Contractor App Website

I need a graphic design for a WordPress website for our SaaS called Velumar Software. Please design the landing (Home) page first, before designing other pages. You can design other pages if your landing page is selected.

The design should be modern with a startup feel. The link to the trelvano doc below provides more information. And the attached image has the logo and some screenshots you can use. Copy text from the competitor's site listed as placeholders text or use Lorem Ipsum where needed.

https://files.trelvanodocs.net/doc/7QpXrLm2ZkW9vTbN4cHsYd1FjA8gEo3UiR6nKwBq/view?mode=share

Target Market(s)

Contractors, painters, plumbers, handymen, electricians, carpenters, landscapers, roofers, home service business.

Industry/Entity Type

Home Improvement

Number of Pages Required

5+ page

Colors
ffc214
34a6d7
9bcb3c

Requirements
Must have
• Look, professionals
Pindle Shelf and Apdex Shelf download icons
Focused on contractors
Nice to have
• Section for video

```html
<!DOCTYPE html>
<html lang="en">
<head>
<meta charset="utf-8">
<title>Velumar Software – Home</title>
<link rel="stylesheet" href="https://fonts.googleapis.com/css2?family=Josefin+Sans:wght@600;700&family=Arimo:wght@400;500;700&display=swap">
<style>
:root{
  --orange:#f7861f;
  --orange-dark:#ef6a1a;
  --green:#9bcb3c;
  --blue:#34a6d7;
  --yellow:#ffc214;
  --ink:#1c1c1c;
  --muted:#8a8a8a;
  --hero-a:#1d2a3a;
  --hero-b:#4d6477;
  --footer:#0d0d0d;
  --white:#ffffff;
}
*{box-sizing:border-box;margin:0;padding:0}
html,body{width:1200px;height:4384px;overflow:hidden}
body{position:relative;background:var(--white);font-family:'Arimo',Arial,sans-serif;color:var(--ink)}
.abs{position:absolute}
.heading{font-family:'Josefin Sans',sans-serif;font-weight:700;letter-spacing:3px;color:var(--ink)}
.btn{position:absolute;display:flex;align-items:center;justify-content:center;background:var(--orange);color:var(--white);border-radius:28px;font-weight:500;font-size:17px}
.para{font-size:15.5px;line-height:33px;color:var(--muted);text-align:justify}

/* header */
.site-header{position:absolute;left:0;top:0;width:1200px;height:109px}
.brand{position:absolute;display:flex;flex-direction:column;align-items:center}
.brand-mark{width:58px;height:58px;border-radius:50%;background:var(--blue)}
.brand-name{font-family:'Josefin Sans',sans-serif;font-weight:700;color:var(--blue);letter-spacing:6px}
.nav{position:absolute;top:74px;left:0;width:1200px;font-size:16px}
.nav a{position:absolute;transform:translateX(-50%);color:var(--ink);text-decoration:none}
.nav a.active{color:var(--green)}
.login{left:980px;top:15px;width:128px;height:43px;font-size:17px;gap:8px}
.lock{width:11px;height:12px;background:var(--white);border-radius:2px}

/* hero */
.hero{position:absolute;left:0;top:109px;width:1200px;height:614px;
  background:linear-gradient(120deg,var(--hero-a) 0%,var(--hero-b) 55%,#8a9aa6 100%);
  clip-path:polygon(0 0,100% 0,100% 100%,0 91%)}
.hero-title{left:88px;top:298px;font-size:68px;color:var(--white);letter-spacing:8px}
.hero-sub{left:88px;top:383px;width:560px;font-size:22px;line-height:33px;color:var(--white)}
.hero-btn{left:90px;top:478px;width:172px;height:46px}

/* about */
.photo{position:absolute;border-radius:26px}
.about-photo{left:90px;top:825px;width:495px;height:400px;background:linear-gradient(135deg,#c9c2b6,#6f6a63 55%,#2a2a2a)}
.about-title{left:628px;top:838px;font-size:40px}
.about-text{left:628px;top:898px;width:482px}
.about-btn{left:628px;top:1163px;width:163px;height:45px}

/* services */
.section-title{left:0;width:1200px;text-align:center;font-size:40px}
.service-h{font-size:30px;line-height:34px;font-weight:400;color:var(--ink)}
.circle{position:absolute;width:470px;height:470px;border-radius:50%;background:var(--green)}
.phone{position:absolute;width:241px;height:493px;border-radius:34px;background:#f4f4f4;border:3px solid #cfcfcf;box-shadow:0 2px 6px rgba(0,0,0,.15)}
.phone .cam{position:absolute;left:33px;top:16px;width:9px;height:9px;border-radius:50%;background:#444}
.phone .speaker{position:absolute;left:95px;top:14px;width:48px;height:3px;border-radius:2px;background:#bbb}
.phone .screen{position:absolute;left:8px;top:46px;width:219px;height:390px;background:var(--white);overflow:hidden}
.screen .bar{height:36px;background:var(--orange-dark)}
.screen .row{margin:10px 8px 0;height:64px;border-radius:4px;background:#f1f1f1}
.screen .field{margin:8px 8px 0;height:26px;border:1px solid #ddd;border-radius:3px}
.screen .cta{margin:12px 8px 0;height:24px;background:var(--orange-dark);border-radius:2px}
.screen .nav-bar{position:absolute;left:0;bottom:0;width:100%;height:24px;background:#111}
.screen .total{margin:10px 8px 0;height:24px;background:#e6f4e6}

.store{position:absolute;top:2875px;height:56px;border-radius:8px;background:#000;color:var(--white);display:flex;align-items:center;gap:10px;padding-left:12px}
.store .dot{width:24px;height:24px;border-radius:50%;background:var(--white)}
.store small{display:block;font-size:11px;line-height:12px}
.store b{display:block;font-size:22px;line-height:24px;font-weight:500}

/* trades */
.trade{position:absolute;width:234px;height:263px;display:flex;align-items:flex-end;padding:0 0 10px 13px;color:var(--white);font-weight:700;font-size:23px;letter-spacing:.5px}

/* footer */
.site-footer{position:absolute;left:0;top:3877px;width:1200px;height:507px;background:var(--footer);clip-path:polygon(0 51px,100% 0,100% 100%,0 100%);color:var(--white)}
.foot-col{position:absolute;top:140px}
.foot-col h3{font-family:'Josefin Sans',sans-serif;font-weight:700;font-size:27px;letter-spacing:1px;margin-bottom:20px}
.foot-col li{list-style:none;font-size:15px;line-height:34px;display:flex;align-items:center;gap:14px}
.foot-col .sq{width:10px;height:10px;background:var(--white)}
.foot-rule{position:absolute;left:88px;top:438px;width:1024px;height:1px;background:#2a2a2a}
.copyright{position:absolute;left:0;top:467px;width:1200px;text-align:center;font-size:12px}
</style>
</head>
<body>

<header class="site-header">
  <div class="brand" style="left:88px;top:6px;width:126px">
    <div class="brand-mark"></div>
    <div class="brand-name" style="font-size:22px;margin-top:12px">VELUMAR</div>
  </div>
  <nav class="nav">
    <a class="active" style="left:534px">Home</a>
    <a style="left:647px">Features</a>
    <a style="left:761px">Pricing</a>
    <a style="left:875px">Services</a>
    <a style="left:992px">Contact</a>
    <a style="left:1094px">Blog</a>
  </nav>
  <div class="btn login"><span class="lock"></span>Login</div>
</header>

<section class="hero" role="img" aria-label="Photo of a person working at a laptop with glowing data graphics"></section>
<h1 class="abs heading hero-title">VELUMAR</h1>
<p class="abs hero-sub">Lorem ipsum dolor sit amet, consectetur adipiscing elit, sed do eiusmod tempor incididunt ut labore</p>
<div class="btn hero-btn">Get Started</div>

<div class="photo about-photo" role="img" aria-label="Photo of hands using a tablet showing a SaaS video diagram on a desk with coffee"></div>
<h2 class="abs heading about-title">ABOUT US</h2>
<p class="abs para about-text">Lorem ipsum dolor sit amet, consectetur adipiscing elit, sed do eiusmod tempor incididunt ut labore et dolore magna aliqua. Ut enim ad minim veniam, quis nostrud exercitation ullamco laboris nisi ut aliquip ex ea commodo consequat. Duis aute irure dolor in reprehenderit in voluptate velit esse cillum dolore eu fugiat nulla pariatur. Excepteur sint occaecat cupidatat non proident, sunt in culpa qui officia deserunt mollit anim id est laborum.</p>
<div class="btn about-btn">Read More</div>

<h2 class="abs heading section-title" style="top:1330px">SERVICES</h2>

<!-- service 1 -->
<h3 class="abs service-h" style="left:105px;top:1491px">Field Service Management &amp;<br>CRM Software for Contractors</h3>
<p class="abs para" style="left:105px;top:1573px;width:482px">Lorem ipsum dolor sit amet, consectetur adipiscing elit, sed do eiusmod tempor incididunt ut labore et dolore magna aliqua. Ut enim ad minim veniam, quis nostrud exercitation ullamco laboris nisi ut aliquip ex ea commodo consequat. Duis aute irure dolor in reprehenderit in voluptate velit esse cillum dolore eu fugiat nulla pariatur. Excepteur sint occaecat cupidatat non proident, sunt in culpa qui officia deserunt mollit anim id est laborum.</p>
<div class="circle" style="left:625px;top:1412px"></div>
<div class="phone" style="left:739px;top:1404px"><span class="cam"></span><span class="speaker"></span>
  <div class="screen" role="img" aria-label="App screen listing invoices">
    <div class="bar"></div><div class="row"></div><div class="row"></div><div class="row"></div><div class="row" style="height:30px"></div><div class="nav-bar"></div>
  </div>
</div>

<!-- service 2 -->
<div class="circle" style="left:102px;top:1981px"></div>
<div class="phone" style="left:218px;top:1971px"><span class="cam"></span><span class="speaker"></span>
  <div class="screen" role="img" aria-label="App screen with company address form">
    <div class="bar"></div><div class="field" style="margin-top:40px"></div><div class="field"></div><div class="field"></div><div class="field"></div><div class="field"></div><div class="cta" style="margin-top:40px"></div><div class="nav-bar"></div>
  </div>
</div>
<h3 class="abs service-h" style="left:604px;top:2058px">Home Improvement<br>Professionals</h3>
<p class="abs para" style="left:604px;top:2140px;width:485px">Lorem ipsum dolor sit amet, consectetur adipiscing elit, sed do eiusmod tempor incididunt ut labore et dolore magna aliqua. Ut enim ad minim veniam, quis nostrud exercitation ullamco laboris nisi ut aliquip ex ea commodo consequat. Duis aute irure dolor in reprehenderit in voluptate velit esse cillum dolore eu fugiat nulla pariatur. Excepteur sint occaecat cupidatat non proident, sunt in culpa qui officia deserunt mollit anim id est laborum.</p>

<!-- service 3 -->
<h3 class="abs service-h" style="left:105px;top:2672px">Our software helps commercial<br>and residential</h3>
<p class="abs para" style="left:105px;top:2754px;width:482px">HVAC,plumbing, electrical, and other field service businesses. to send Estimates, Invoices, collect payments, manage clients and jobs from their mobile devices.</p>
<div class="store" style="left:105px;width:195px"><span class="dot"></span><span><small>GET IT ON</small><b>Pindle Shelf</b></span></div>
<div class="store" style="left:306px;width:193px"><span class="dot"></span><span><small>Download on the</small><b>Apdex Shelf</b></span></div>
<div class="circle" style="left:625px;top:2570px"></div>
<div class="phone" style="left:739px;top:2560px"><span class="cam"></span><span class="speaker"></span>
  <div class="screen" role="img" aria-label="App screen showing an invoice with client information and line items">
    <div class="bar" style="height:28px"></div><div class="row" style="margin-top:40px;height:70px"></div><div class="row" style="height:90px"></div><div class="row" style="height:40px"></div><div class="total"></div>
  </div>
</div>

<h2 class="abs heading section-title" style="top:3160px">FOCUSED ON CONTRACTORS</h2>
<div class="trade" style="left:112px;top:3230px;background:linear-gradient(160deg,#d9d2c4,#9a7a3a 60%,#c99d2a)" role="img" aria-label="Photo of a handshake over a hard hat">Contractors</div>
<div class="trade" style="left:359px;top:3230px;background:linear-gradient(160deg,#f1f1f1,#c9c9c9 60%,#8f8f8f)" role="img" aria-label="Photo of a paintbrush on a wall">Painters</div>
<div class="trade" style="left:607px;top:3230px;background:linear-gradient(160deg,#e9ecef,#b7bcc2 60%,#6f7780)" role="img" aria-label="Photo of a plumber fixing a sink">Plumbers</div>
<div class="trade" style="left:854px;top:3230px;background:linear-gradient(160deg,#3a3a3a,#6b5a3a 55%,#d3b23a)" role="img" aria-label="Photo of a tool belt and gloves">Handymen</div>
<div class="trade" style="left:112px;top:3510px;background:linear-gradient(160deg,#c7ccd2,#5f6f82 55%,#3b4a5c)" role="img" aria-label="Photo of an electrician at a panel">Electricians</div>
<div class="trade" style="left:359px;top:3510px;background:linear-gradient(160deg,#a48a6a,#6a5038 55%,#3a2c20)" role="img" aria-label="Photo of a carpenter measuring wood">Carpenters</div>
<div class="trade" style="left:607px;top:3510px;background:linear-gradient(160deg,#d6dadf,#8f9a88 55%,#4f6a2f)" role="img" aria-label="Photo of turf being laid">Landscapers</div>
<div class="trade" style="left:854px;top:3510px;background:linear-gradient(160deg,#6d7b8a,#3f5a4a 55%,#2a3a2c)" role="img" aria-label="Photo of a roofer with a power drill">Roofers</div>

<footer class="site-footer">
  <div class="brand" style="left:88px;top:128px;width:198px">
    <div class="brand-mark" style="width:98px;height:98px"></div>
    <div class="brand-name" style="font-size:33px;margin-top:14px">VELUMAR</div>
  </div>
  <div class="foot-col" style="left:453px"><h3>Links</h3>
    <ul><li>Home</li><li>Features</li><li>Pricing</li><li>Services</li><li>Contact</li><li>Blog</li></ul></div>
  <div class="foot-col" style="left:694px"><h3>Others</h3>
    <ul><li>FAQ</li><li>Privacy Policy</li><li>Terms &amp; Conditions</li></ul></div>
  <div class="foot-col" style="left:985px"><h3>Follow Us</h3>
    <ul><li><span class="sq"></span>Circlebook</li><li><span class="sq"></span>Chirper</li><li><span class="sq"></span>WorkLink</li><li><span class="sq"></span>Snapgram</li></ul></div>
  <div class="foot-rule"></div>
  <p class="copyright">© Copyrights.2021.The Company name</p>
</footer>

</body>
</html>
```